Corporate Design für die Vela Serena! GmbH
Zielgruppe
Die Vela Serena! GmbH begibt sich auf den Weg mit den Firmen, die sie gründet, kauft, entwickelt und verkauft. Wir sind eine Holding, beteiligen uns an Firmen oder gründen diese neu. 'Vela Serena!' ist der Pilgergruß auf dem Jakobsweg - diesen bin ich schon 5 Mal gegangen und die Metapher 'Gründen als Weg/Pilgerreise' finde ich sehr zutreffend. Ferner gibt es einen gelben Pfeil auf dem Jakobsweg, der einen immer verfolgt und einem den Weg weist. Das sind wir auch.
Aufgabenstellung
Es ist am Ende das Tages eine Holding, bei der sich Gründer und Firmen melden sollen, weil sie Beratung oder Kapital brauchen - daher ist Seriosität zwar unbedingt notwendig aber sie soll nicht abschrecken, elitär, 'Anwalt-grau-blau-weiß-bieder' sein. Gründertum, Unternehmertum, Freude, Machen, Erfolg!
Pilgern macht Freude und Gründen und Firmen haben auch. Mit uns um so mehr! Ein toller Weg!
'Vela Serena!' eben
Wir heißen 'Vela Serena! GmbH' - mit einem Ausrufezeichen angemeldet und das ist wichtig. Wir haben keine 'Fragezeichen' oder 'Punkte' wir haben ein Ausrufezeichen und einen Pfeil, ein Ziel, einen Weg, Etappen...
Die Abkürzung 'VS!' kann eine Möglichkeit sein aber ausgeschrieben wäre mir lieber - VS! kann das Favicon oder eine Logo-Kurzform/Variante sein

```html
<!DOCTYPE html>
<html lang="de">
<head>
<meta charset="utf-8">
<title>Vela Serena! GmbH – Corporate Design</title>
<link rel="stylesheet" href="https://fonts.googleapis.com/css2?family=Questrial&family=Nunito+Sans:wght@400;600;700&display=swap">
<style>
:root{
  --ink:#333333;
  --blue:#2c5aa0;
  --yellow:#fdc300;
  --paper:#ffffff;
  --faint:#e9ecf1;
  --grey:#cccccc;
}
*{margin:0;padding:0;box-sizing:border-box}
html,body{width:1200px;height:4307px;overflow:hidden;background:var(--paper)}
body{position:relative;font-family:"Nunito Sans",sans-serif;color:var(--ink)}
.abs{position:absolute}
.wordmark{font-family:"Questrial",sans-serif;letter-spacing:.02em;white-space:nowrap;line-height:1}
.dot{border-radius:50%;position:absolute}
.sheet{position:absolute;background:var(--paper);box-shadow:4px 6px 14px rgba(0,0,0,.18);overflow:hidden}
.bar-top{position:absolute;left:0;right:0;top:0;height:12px;background:var(--ink)}
.bar-bottom{position:absolute;left:0;right:0;bottom:0;height:12px;background:var(--blue)}
.contact{position:absolute;font-size:14px;line-height:21.5px}
.contact li{list-style:none;display:flex;align-items:center;gap:10px;white-space:nowrap}
.contact svg{width:12px;height:12px;fill:currentColor;flex:none}
.card .contact{font-size:11.5px;line-height:18px}
.card .contact svg{width:10px;height:10px}
.name{font-weight:700;font-size:15px;line-height:1}
.role{font-size:12px}
.addr{font-size:11.5px;line-height:15px}
</style>
</head>
<body>

<!-- Master brand -->
<section class="brand-master">
  <div class="dot" style="left:475px;top:113px;width:250px;height:250px;background:var(--blue)"></div>
  <div class="abs wordmark" style="left:0;width:1200px;top:410px;text-align:center;font-size:118px;color:var(--ink)">VELA SERENA!</div>
</section>

<!-- Letterhead -->
<section class="sheet letterhead" style="left:83px;top:807px;width:1007px;height:1421px">
  <div class="bar-top"></div>
  <div class="dot" style="left:757px;top:60px;width:80px;height:80px;background:var(--blue)"></div>
  <div class="abs wordmark" style="left:457px;width:500px;text-align:right;top:152px;font-size:38px">VELA SERENA!</div>

  <div class="abs" style="left:105px;top:210px;width:412px;height:216px">
    <div class="abs" style="left:0;top:0;width:10px;height:10px;border-left:1px solid var(--ink);border-top:1px solid var(--ink)"></div>
    <div class="abs" style="right:0;top:0;width:10px;height:10px;border-right:1px solid var(--ink);border-top:1px solid var(--ink)"></div>
    <div class="abs" style="left:0;bottom:0;width:10px;height:10px;border-left:1px solid var(--ink);border-bottom:1px solid var(--ink)"></div>
    <div class="abs" style="right:0;bottom:0;width:10px;height:10px;border-right:1px solid var(--ink);border-bottom:1px solid var(--ink)"></div>
    <p class="abs sender" style="left:12px;top:10px;font-size:11.5px;white-space:nowrap">Vela Serena! GmbH | Musterstrasse 123 | 12345 Musterstadt</p>
  </div>

  <ul class="contact" style="left:762px;top:214px">
    <li><svg viewBox="0 0 12 12"><path d="M2 1l2 0 1 3-1.5 1a6 6 0 0 0 3 3L8 6.5l3 1v2.5a1 1 0 0 1-1 1A9 9 0 0 1 1 2a1 1 0 0 1 1-1z"/></svg>+41 200 / 11 22 33 44</li>
    <li><svg viewBox="0 0 12 12"><rect x="3" y="1" width="6" height="4"/><rect x="1" y="5" width="10" height="5" rx="1"/></svg>+41 200 / 11 22 33 45</li>
    <li><svg viewBox="0 0 12 12"><rect x="1" y="2.5" width="10" height="7"/><path d="M1 2.5l5 4 5-4" stroke="#fff" fill="none"/></svg>info@vela-serena.de</li>
    <li><svg viewBox="0 0 12 12"><circle cx="6" cy="6" r="5"/><path d="M1 6h10M6 1v10" stroke="#fff"/></svg>www.vela-serena.de</li>
  </ul>

  <div class="abs" style="left:0;top:496px;width:12px;height:1px;background:var(--ink)"></div>
  <div class="abs" style="left:0;top:1000px;width:12px;height:1px;background:var(--ink)"></div>

  <div class="dot" style="left:331px;top:568px;width:366px;height:366px;background:var(--faint)"></div>

  <footer class="abs" style="left:0;right:0;bottom:0;height:98px;border-top:4px solid var(--yellow);background:var(--blue);color:#fff;font-size:14px;line-height:18.5px">
    <div class="abs" style="left:95px;top:14px;border-left:1px solid #fff;padding-left:8px">Musterstrasse 123<br>12345 Musterstadt<br>Geschäftsführung Max Muster</div>
    <div class="abs" style="left:379px;top:14px;border-left:1px solid #fff;padding-left:8px">Bankverbindung<br>BIC:&nbsp;&nbsp;ABCDEFGHXXX<br>IBAN: DE 00 0000 0000 0000 0000 00</div>
    <div class="abs" style="left:755px;top:14px;border-left:1px solid #fff;padding-left:8px">Finanzamt<br>Musterstadt<br>USt-IdNr.: DE000000000</div>
  </footer>
</section>

<!-- Business card front, blue -->
<section class="sheet card" style="left:95px;top:2310px;width:478px;height:310px;background:var(--blue)">
  <div class="dot" style="left:250px;top:50px;width:300px;height:300px;background:rgba(255,255,255,.06)"></div>
  <div class="dot" style="left:197px;top:82px;width:84px;height:84px;background:#fff"></div>
  <div class="abs wordmark" style="left:0;width:478px;text-align:center;top:182px;font-size:46px;color:#fff">VELA SERENA!</div>
</section>

<!-- Business card back, blue panel -->
<section class="sheet card" style="left:622px;top:2310px;width:480px;height:310px">
  <div class="abs" style="left:240px;top:0;right:0;bottom:0;background:var(--blue);color:#fff">
    <div class="dot" style="left:96px;top:28px;width:48px;height:48px;background:#fff"></div>
    <div class="abs wordmark" style="left:0;width:240px;text-align:center;top:88px;font-size:26px">VELA SERENA!</div>
    <ul class="contact" style="left:18px;top:206px">
      <li><svg viewBox="0 0 12 12"><path d="M2 1l2 0 1 3-1.5 1a6 6 0 0 0 3 3L8 6.5l3 1v2.5a1 1 0 0 1-1 1A9 9 0 0 1 1 2a1 1 0 0 1 1-1z"/></svg>+41 200 / 11 22 33 44</li>
      <li><svg viewBox="0 0 12 12"><rect x="3" y="1" width="6" height="4"/><rect x="1" y="5" width="10" height="5" rx="1"/></svg>+41 200 / 11 22 33 45</li>
      <li><svg viewBox="0 0 12 12"><rect x="3.5" y="0.5" width="5" height="11" rx="1"/></svg>+41 200 / 11 22 33 46</li>
      <li><svg viewBox="0 0 12 12"><rect x="1" y="2.5" width="10" height="7"/></svg>info@vela-serena.de</li>
      <li><svg viewBox="0 0 12 12"><circle cx="6" cy="6" r="5"/></svg>www.vela-serena.de</li>
    </ul>
  </div>
  <div class="abs" style="left:13px;top:166px"><p class="name">MAX MUSTER</p><p class="role">Patentanwalt</p></div>
  <p class="abs addr" style="left:13px;top:266px">Musterstrasse 123<br>12345 Musterstadt</p>
</section>

<!-- Business card front, white -->
<section class="sheet card" style="left:95px;top:2693px;width:478px;height:310px">
  <div class="bar-top"></div>
  <div class="dot" style="left:200px;top:40px;width:320px;height:320px;background:#efefef"></div>
  <div class="dot" style="left:197px;top:82px;width:84px;height:84px;background:var(--blue)"></div>
  <div class="abs wordmark" style="left:0;width:478px;text-align:center;top:182px;font-size:46px">VELA SERENA!</div>
  <div class="bar-bottom"></div>
</section>

<!-- Business card back, white -->
<section class="sheet card" style="left:622px;top:2693px;width:480px;height:310px">
  <div class="bar-top"></div>
  <div class="dot" style="left:325px;top:40px;width:52px;height:52px;background:var(--blue)"></div>
  <div class="abs wordmark" style="left:180px;width:282px;text-align:right;top:100px;font-size:28px">VELA SERENA!</div>
  <div class="abs" style="left:13px;top:166px"><p class="name">MAX MUSTER</p><p class="role">Patentanwalt</p></div>
  <p class="abs addr" style="left:13px;top:266px">Musterstrasse 123<br>12345 Musterstadt</p>
  <ul class="contact" style="left:302px;top:198px">
    <li><svg viewBox="0 0 12 12"><path d="M2 1l2 0 1 3-1.5 1a6 6 0 0 0 3 3L8 6.5l3 1v2.5a1 1 0 0 1-1 1A9 9 0 0 1 1 2a1 1 0 0 1 1-1z"/></svg>+41 200 / 11 22 33 44</li>
    <li><svg viewBox="0 0 12 12"><rect x="3" y="1" width="6" height="4"/><rect x="1" y="5" width="10" height="5" rx="1"/></svg>+41 200 / 11 22 33 45</li>
    <li><svg viewBox="0 0 12 12"><rect x="3.5" y="0.5" width="5" height="11" rx="1"/></svg>+41 200 / 11 22 33 46</li>
    <li><svg viewBox="0 0 12 12"><rect x="1" y="2.5" width="10" height="7"/></svg>info@vela-serena.de</li>
    <li><svg viewBox="0 0 12 12"><circle cx="6" cy="6" r="5"/></svg>www.vela-serena.de</li>
  </ul>
  <div class="bar-bottom"></div>
</section>

<!-- Envelope front -->
<section class="sheet envelope" style="left:88px;top:3117px;width:1019px;height:508px">
  <div class="bar-top"></div>
  <div class="dot" style="left:260px;top:120px;width:58px;height:58px;background:var(--blue)"></div>
  <div class="abs wordmark" style="left:90px;width:400px;text-align:center;top:186px;font-size:30px">VELA SERENA!</div>
  <div class="abs window" style="left:90px;top:243px;width:397px;height:198px;border-radius:22px;background:var(--grey)"></div>
  <div class="bar-bottom"></div>
</section>

<!-- Envelope back -->
<section class="sheet envelope" style="left:88px;top:3697px;width:1019px;height:508px">
  <svg class="abs flap" style="left:0;top:0" width="1019" height="146" viewBox="0 0 1019 146">
    <path d="M0 0H1019L974 120Q964 146 936 146H83Q55 146 45 120Z" fill="var(--ink)"/>
  </svg>
  <div class="dot" style="left:483px;top:20px;width:54px;height:54px;background:#fff"></div>
  <div class="abs wordmark" style="left:0;width:1019px;text-align:center;top:96px;font-size:36px;color:#fff">VELA SERENA!</div>
  <div class="bar-bottom"></div>
</section>

</body>
</html>
```